K & R Acre Works. Business card design

We need a business card designed for a new business. We have a bulldozer and tractor service. We clear land and make wildlife food plots. We provide disking, bush hogging, and site prep services.
I have attached an image of a business card that I like and would like my business cards to look similar.

Target Market(s)

anyone needing bulldozer and/or tractor services

Industry/Entity Type

Business

Contact Information for Business Card

K & R Acre Works, Operated by 7-T-Ranch
Wade Colton
601-472-3358
wcr4817@fieldmail-example.com

Font styles to use
Sans Serif

Colors

Designer to choose colors to be used in the design.

Requirements
Must have
• image of tractor and bulldozer
• Land Clearing
• Wildlife food plots
• Bush Hogging
• Disking
• Site prep
Nice to have
• i have included a image of a business card that i like. I would like mine to be similar.

```html
<!DOCTYPE html>
<html lang="en">
<head>
<meta charset="utf-8">
<title>K &amp; R Acre Works – Business Card</title>
<link rel="stylesheet" href="https://fonts.googleapis.com/css2?family=Oswald:wght@300;500;600&family=Roboto:wght@300;400&display=swap">
<style>
  :root {
    --page-bg: #e9e6e1;
    --card-black: #0c0c0c;
    --accent-red: #e8524a;
    --accent-red-dark: #b5201b;
    --text-white: #ffffff;
    --text-soft: #e6e6e6;
    --photo-green: #5c7a3a;
    --photo-dark: #2c3a1f;
    --photo-yellow: #b99a2e;
  }
  html, body {
    margin: 0;
    width: 1200px;
    height: 1023px;
    overflow: hidden;
    background: var(--page-bg);
  }
  .card-stage {
    width: 1200px;
    height: 1023px;
    display: flex;
    align-items: center;
    justify-content: center;
  }
  .business-card {
    display: block;
    filter: drop-shadow(0 14px 28px rgba(0,0,0,0.25));
  }
  .brand-name {
    font-family: 'Oswald', sans-serif;
    font-weight: 600;
    font-size: 64px;
    fill: var(--text-white);
    letter-spacing: 1px;
  }
  .brand-operator {
    font-family: 'Oswald', sans-serif;
    font-weight: 300;
    font-size: 26px;
    fill: var(--text-soft);
    letter-spacing: 9px;
  }
  .owner-name {
    font-family: 'Oswald', sans-serif;
    font-weight: 600;
    font-size: 64px;
    fill: var(--accent-red);
    letter-spacing: 1px;
  }
  .contact-line {
    font-family: 'Roboto', sans-serif;
    font-weight: 300;
    font-size: 36px;
    fill: var(--text-white);
  }
  .service-line {
    font-family: 'Oswald', sans-serif;
    font-weight: 500;
    font-size: 28px;
    fill: var(--text-white);
    letter-spacing: 0.5px;
  }
  .contact-icon {
    fill: none;
    stroke: var(--accent-red);
    stroke-width: 3;
    stroke-linecap: round;
    stroke-linejoin: round;
  }
</style>
</head>
<body>
<main class="card-stage">
  <svg class="business-card" width="1050" height="600" viewBox="0 0 1050 600" xmlns="http://www.w3.org/2000/svg">
    <defs>
      <clipPath id="card-shape">
        <rect x="0" y="0" width="1050" height="600" rx="26" ry="26"/>
      </clipPath>
      <linearGradient id="photo-tones" x1="0" y1="0" x2="1" y2="1">
        <stop offset="0" stop-color="var(--photo-green)"/>
        <stop offset="0.45" stop-color="var(--photo-yellow)"/>
        <stop offset="0.7" stop-color="var(--photo-dark)"/>
        <stop offset="1" stop-color="var(--photo-green)"/>
      </linearGradient>
      <linearGradient id="title-shade" x1="0" y1="0" x2="0" y2="1">
        <stop offset="0" stop-color="#000" stop-opacity="0.35"/>
        <stop offset="1" stop-color="#000" stop-opacity="0"/>
      </linearGradient>
      <linearGradient id="red-sweep" x1="0" y1="0" x2="1" y2="0">
        <stop offset="0" stop-color="var(--accent-red-dark)"/>
        <stop offset="0.5" stop-color="var(--accent-red)"/>
        <stop offset="1" stop-color="var(--accent-red-dark)"/>
      </linearGradient>
    </defs>

    <g clip-path="url(#card-shape)">
      <rect class="card-base" width="1050" height="600" fill="var(--card-black)"/>

      <path class="photo-area" role="img" aria-label="Photo of a yellow bulldozer working in green brush"
            d="M0 0 H1050 V150 Q620 330 0 300 Z" fill="url(#photo-tones)"/>
      <rect class="title-shade" width="1050" height="180" fill="url(#title-shade)"/>

      <path class="accent-curve" d="M0 300 Q620 330 1050 150" fill="none" stroke="url(#red-sweep)" stroke-width="12"/>

      <text class="brand-name" x="60" y="88">K &amp; R ACRE WORKS</text>
      <text class="brand-operator" x="62" y="128">OPERATED BY 7-T-RANCH</text>

      <text class="owner-name" x="60" y="395">WADE COLTON</text>

      <path class="contact-icon" d="M84 424 q-10 8 -4 21 q6 13 18 15"/>
      <text class="contact-line" x="116" y="452">601-472-3358</text>

      <g class="contact-icon">
        <rect x="76" y="475" width="26" height="19" rx="2"/>
        <path d="M76 477 L89 487 L102 477"/>
      </g>
      <text class="contact-line" x="116" y="498">wcr4817@fieldmail-example.com</text>

      <text class="service-line" x="60" y="544">LAND CLEARING - WILDLIFE FOOD PLOTS</text>
      <text class="service-line" x="60" y="578">BUSH HOGGING - DISKING - SITE PREP</text>
    </g>
  </svg>
</main>
</body>
</html>
```